Professional Website for Leading Global Private Equity Real Estate Company

The company is a leading global Private Equity Real Estate (PERE). We need a homepage design, an inner page design, and color/font tweaks to the logo (color should be more soothing than current blue used in the logo). The logo website should project the company as global, professional, experienced, trustworthy, accessible, YOUNG, DYNAMIC, hi-tech. PLEASE SEE the attached Design Brief Word Doc for details.

Target Market(s)

institional investors and wealthy private individuals

Industry/Entity Type

Finance

Number of Pages Required

2 page

Font styles to use
Sans Serif
Other font styles liked:
• either like in https://www.ferndalequay.com/ or like in presentations (Montserrat Black & Montserrat Light, Century Gothic, Blair ITC, Almoni Neue DL 4.0 AAA Medium, Almoni DL AAA)

Requirements
Must have
• new color palette that is NOT based on current logo. they want a more soothing color palette than the blue in that logo. the new color palette should project: global, professional, experienced, trustworthy, accessible, YOUNG, DYNAMIC, hi-tech.
Nice to have
• the likes these sites: https://www.ferndalequay.com/ and https://www.tvr.law/

```html
<!DOCTYPE html>
<html lang="en">
<head>
<meta charset="utf-8">
<title>Veltara Real Estate – Page Headers</title>
<link rel="stylesheet" href="https://fonts.googleapis.com/css2?family=Michroma&family=Roboto:wght@300;400&display=swap">
<style>
  :root {
    --white: #ffffff;
    --navy: #1c2a47;
    --slate-dark: #26282d;
    --slate-mid: #5f6268;
    --slate-light: #a3a5aa;
    --dusk-blue: #2a4260;
    --dusk-warm: #7a6a70;
    --sky-lilac: #8a8ca6;
    --tower-dark: #1a2030;
    --nav-shade: rgba(22, 28, 42, 0.5);
  }
  * { box-sizing: border-box; margin: 0; padding: 0; }
  html, body { width: 1200px; height: 2221px; overflow: hidden; background: var(--white); }
  body { position: relative; font-family: "Roboto", Arial, sans-serif; color: var(--white); }

  .hero { position: absolute; left: 0; width: 1200px; overflow: hidden; }
  .hero-photo { position: absolute; inset: 0; }

  .hero--about-mono { top: 0; height: 462px; }
  .hero--about-mono .hero-photo {
    background:
      radial-gradient(ellipse 260px 340px at 640px 230px, rgba(200,202,206,0.55) 0%, rgba(200,202,206,0) 100%),
      linear-gradient(90deg, #1c1d21 0%, #3a3c41 18%, var(--slate-mid) 34%, #8d8f94 50%, var(--slate-mid) 66%, #3a3c41 84%, #1c1d21 100%);
  }

  .hero--investor { top: 565px; height: 469px; }
  .hero--investor .hero-photo {
    background:
      radial-gradient(ellipse 220px 300px at 560px 250px, rgba(150,152,180,0.9) 0%, rgba(150,152,180,0) 100%),
      linear-gradient(90deg, var(--tower-dark) 0%, #2b3348 22%, #5b6078 40%, var(--sky-lilac) 50%, #5b6078 62%, #2b3348 80%, var(--tower-dark) 100%);
  }

  .hero--about-navy { top: 1131px; height: 484px; background: var(--navy); }
  .hero--about-navy .hero-photo {
    left: 450px;
    background:
      radial-gradient(ellipse 260px 160px at 330px 440px, rgba(140,100,60,0.35) 0%, rgba(140,100,60,0) 100%),
      linear-gradient(100deg, var(--navy) 0%, #2a3a5a 30%, #3d5274 55%, #6f829f 80%, #9aa7bb 100%);
  }

  .hero--about-city { top: 1678px; height: 462px; }
  .hero--about-city .hero-photo {
    background:
      linear-gradient(180deg, #4f586f 0%, var(--dusk-warm) 14%, var(--dusk-blue) 24%, #2f4560 38%, #3c4f66 60%, #6b5d66 82%, #8a6a6a 100%);
  }

  .site-nav { position: absolute; left: 0; top: 0; width: 1200px; height: 76px; }
  .site-nav--band { height: 90px; background: var(--nav-shade); }
  .hero--about-navy .site-nav { left: -5px; }

  .brand { position: absolute; left: 102px; top: 7px; display: flex; align-items: center; gap: 12px; }
  .brand-mark { width: 52px; height: 52px; border-radius: 50%; background: var(--white); }
  .brand-name { font-family: "Roboto", Arial, sans-serif; font-weight: 300; font-size: 20px; line-height: 25px; letter-spacing: 0.4px; text-transform: uppercase; }

  .nav-links { position: absolute; top: 30px; left: 0; list-style: none; font-size: 14.5px; font-weight: 400; letter-spacing: 0.3px; text-transform: uppercase; }
  .nav-links li { position: absolute; white-space: nowrap; display: flex; align-items: center; gap: 5px; }
  .nav-links svg { width: 11px; height: 7px; }

  .login-btn { position: absolute; left: 1010px; top: 20px; width: 98px; height: 34px; border: 1.5px solid var(--white); border-radius: 17px; font-size: 13px; display: flex; align-items: center; justify-content: center; text-transform: uppercase; letter-spacing: 0.3px; }

  .hero-title { position: absolute; font-family: "Michroma", "Syncopate", Verdana, sans-serif; font-weight: 400; font-size: 37px; line-height: 41px; text-transform: uppercase; letter-spacing: 0.5px; white-space: nowrap; }
  .hero-title--center { left: 0; width: 1200px; text-align: center; }
</style>
</head>
<body>

<section class="hero hero--about-mono">
  <div class="hero-photo" role="img" aria-label="Black and white view looking up between office towers"></div>
  <nav class="site-nav">
    <div class="brand"><span class="brand-mark"></span><span class="brand-name">Veltara<br>Real Estate</span></div>
    <ul class="nav-links">
      <li style="left:356px">About Us <svg viewBox="0 0 11 7"><path d="M1 1l4.5 4.5L10 1" fill="none" stroke="#fff" stroke-width="1.4"/></svg></li>
      <li style="left:466px">Our Businesses <svg viewBox="0 0 11 7"><path d="M1 1l4.5 4.5L10 1" fill="none" stroke="#fff" stroke-width="1.4"/></svg></li>
      <li style="left:628px">Investors Lobby</li>
      <li style="left:793px">News</li>
      <li style="left:880px">Contact Us</li>
    </ul>
    <div class="login-btn">Log In</div>
  </nav>
  <h1 class="hero-title hero-title--center" style="top:202px">About Veltara<br>Realestate</h1>
</section>

<section class="hero hero--investor">
  <div class="hero-photo" role="img" aria-label="Glass skyscrapers seen from below against a dusky sky"></div>
  <nav class="site-nav site-nav--band">
    <div class="brand"><span class="brand-mark"></span><span class="brand-name">Veltara<br>Real Estate</span></div>
    <ul class="nav-links">
      <li style="left:356px">About Us <svg viewBox="0 0 11 7"><path d="M1 1l4.5 4.5L10 1" fill="none" stroke="#fff" stroke-width="1.4"/></svg></li>
      <li style="left:466px">Our Businesses <svg viewBox="0 0 11 7"><path d="M1 1l4.5 4.5L10 1" fill="none" stroke="#fff" stroke-width="1.4"/></svg></li>
      <li style="left:628px">Investors Lobby</li>
      <li style="left:793px">News</li>
      <li style="left:880px">Contact Us</li>
    </ul>
    <div class="login-btn">Log In</div>
  </nav>
  <h1 class="hero-title" style="left:118px;top:197px">Investor<br>Lobby</h1>
</section>

<section class="hero hero--about-navy">
  <div class="hero-photo" role="img" aria-label="Modern office towers at dusk with lit windows"></div>
  <nav class="site-nav">
    <div class="brand"><span class="brand-mark"></span><span class="brand-name">Veltara<br>Real Estate</span></div>
    <ul class="nav-links">
      <li style="left:356px">About Us <svg viewBox="0 0 11 7"><path d="M1 1l4.5 4.5L10 1" fill="none" stroke="#fff" stroke-width="1.4"/></svg></li>
      <li style="left:466px">Our Businesses <svg viewBox="0 0 11 7"><path d="M1 1l4.5 4.5L10 1" fill="none" stroke="#fff" stroke-width="1.4"/></svg></li>
      <li style="left:628px">Investors Lobby</li>
      <li style="left:793px">News</li>
      <li style="left:880px">Contact Us</li>
    </ul>
    <div class="login-btn">Log In</div>
  </nav>
  <h1 class="hero-title" style="left:112px;top:209px">About Veltara<br>Realestate</h1>
</section>

<section class="hero hero--about-city">
  <div class="hero-photo" role="img" aria-label="Aerial view of a lakeside city skyline at dusk"></div>
  <nav class="site-nav site-nav--band">
    <div class="brand"><span class="brand-mark"></span><span class="brand-name">Veltara<br>Real Estate</span></div>
    <ul class="nav-links">
      <li style="left:356px">About Us <svg viewBox="0 0 11 7"><path d="M1 1l4.5 4.5L10 1" fill="none" stroke="#fff" stroke-width="1.4"/></svg></li>
      <li style="left:466px">Our Businesses <svg viewBox="0 0 11 7"><path d="M1 1l4.5 4.5L10 1" fill="none" stroke="#fff" stroke-width="1.4"/></svg></li>
      <li style="left:628px">Investors Lobby</li>
      <li style="left:793px">News</li>
      <li style="left:880px">Contact Us</li>
    </ul>
    <div class="login-btn">Log In</div>
  </nav>
  <h1 class="hero-title hero-title--center" style="top:193px">About Veltara<br>Realestate</h1>
</section>

</body>
</html>
```